Brochure design for International Beauty Trade Show

I neee a tri-fold company products' brochure to distribute to customers at an international trade show coming soon. We have 4 main product categories- hair and skincare, facial care, Body and bath and massage oil.
The brochure needs to include at least 2 photos of the main products of each category, benefits, call to action and our company contact info ( website and phone number).

Target Market(s)

Educated and high income earners looking for all-natural,pure, 100 organic products for their beauty and personal care needs. Our products cross all racial groups/demographics and suitable for all skin types

Industry/Entity Type

Hair And Beauty

Font styles to use
Serif

Colors

Designer to choose colors to be used in the design.

Requirements
Must have
• The design must stand out as pure and luxury and at the same time be inclusive using our logo design colors- orange and blue. Also, the content must be easy to read and captivating.
• Finally if using women pictures, please include Black, white, Asian and Latina to reflect the fact that our products are suitable for all skin types.
Nice to have
• Design the brochure such that it could be printed as a poster-banner ad.
Should not have
• Cookie cutter designs are not welcome

```html
<!DOCTYPE html>
<html lang="en">
<head>
<meta charset="utf-8">
<title>Lumera Naturals – Trade Show Brochure</title>
<link href="https://fonts.googleapis.com/css2?family=Montserrat:wght@400;500;600&family=Oswald:wght@300;400;600&family=Roboto+Condensed:wght@400;500&display=swap" rel="stylesheet">
<style>
:root{
  --orange:#f06a13;
  --blue:#1b8fd6;
  --ink:#1e1e1e;
  --grey:#5a5a5a;
  --leaf:#7fbf3a;
  --leaf-soft:#dcefc4;
  --yellow:#f7e41b;
  --bg:#e9e7e3;
  --paper:#ffffff;
}
*{margin:0;padding:0;box-sizing:border-box}
html,body{width:960px;height:1200px;overflow:hidden;background:var(--bg)}
.canvas{position:relative;width:960px;height:1200px}
.panel{position:absolute;left:160px;width:654px;background:var(--paper);overflow:hidden;box-shadow:0 4px 14px rgba(0,0,0,.25)}
.panel--outer{top:86px;height:505px}
.panel--inner{top:636px;height:506px}
.abs{position:absolute}
.photo{position:absolute}

/* outer panel */
.hero-photo{left:205px;top:0;width:449px;height:505px;
  background:radial-gradient(ellipse at 80% 40%,rgba(140,110,80,.55),transparent 55%),
  linear-gradient(180deg,rgba(255,255,255,0) 55%,rgba(70,45,30,.75) 100%),
  linear-gradient(110deg,#ffffff 0%,#f3f8ea 35%,var(--leaf-soft) 55%,var(--leaf) 100%)}
.about-title{left:18px;top:22px;font:600 24px/1 Montserrat,sans-serif;color:var(--orange)}
.about-text{left:18px;top:56px;width:172px;font:400 8.6px/13.2px Montserrat,sans-serif;color:var(--grey)}
.callout{left:14px;top:158px;width:185px;height:42px;background:var(--blue);border-radius:6px;color:#fff;
  font:500 12.4px/15px Montserrat,sans-serif;padding:6px 10px}
.callout::after{content:"";position:absolute;left:8px;bottom:-7px;border:4px solid transparent;border-top:7px solid var(--blue);border-bottom:0}
.range{left:18px;top:216px;list-style:none;font:400 10px/1.2 Montserrat,sans-serif;color:var(--ink)}
.range li{display:flex;align-items:flex-start;gap:6px;height:19.2px}
.range li.tall{height:30px}
.rule{left:18px;top:430px;width:180px;height:1px;background:#bbb}
.order{left:17px;top:442px;display:flex;align-items:center;gap:10px}
.order p{font:600 12.2px/16px Montserrat,sans-serif;color:var(--ink)}
.contact{left:236px;top:34px;width:180px;text-align:center;font-family:Montserrat,sans-serif}
.contact h2{font:600 19px/1 Montserrat,sans-serif;color:var(--blue);margin-bottom:12px}
.contact p{font:500 13.6px/23px Montserrat,sans-serif;color:var(--ink)}
.brand{left:470px;top:58px;display:flex;align-items:center;gap:8px;font:600 15px/1 Montserrat,sans-serif;color:var(--orange)}
.brand i{display:block;width:22px;height:22px;border-radius:50%;background:var(--blue)}
.tagline{right:26px;top:415px;text-align:left;font:600 28px/30px Oswald,sans-serif;color:var(--yellow);text-shadow:1px 1px 2px rgba(0,0,0,.6)}
.tagline span{display:block;color:#fff}

/* inner panel */
.band{left:0;top:0}
.cat{position:absolute;font:400 27px/29px Oswald,sans-serif}
.cat--orange{color:var(--orange)}
.cat--blue{color:var(--blue)}
.line{position:absolute;height:2px}
.line--orange{background:var(--orange)}
.line--blue{background:var(--blue)}
.benefits{position:absolute;list-style:none;font:400 12px/14px "Roboto Condensed",sans-serif;color:var(--ink);letter-spacing:-.1px}
.benefits li{display:flex;align-items:flex-start;gap:7px;height:21px}
.benefits li.tall{height:35px}
.benefits svg{flex:none;margin-top:1px}
</style>
</head>
<body>
<div class="canvas">

  <section class="panel panel--outer">
    <div class="photo hero-photo" role="img" aria-label="Two women with long glossy hair, one holding a jar of cream, in front of green bamboo stalks"></div>

    <h1 class="abs about-title">About us</h1>
    <p class="abs about-text">Lumera Naturals is an export/import company. Our mission is to satisfy our customers by supplying them with pure, 100% organic products, that make them more attractive and solve the most common skin and hair problems</p>

    <div class="abs callout">Over 20 luxury Products<br>to choose from including:</div>

    <ul class="abs range">
      <li><svg width="11" height="11" viewBox="0 0 11 11"><rect x=".5" y="1.5" width="9" height="9" fill="none" stroke="#1b8fd6"/><path d="M2.5 6l2 2 5-7" fill="none" stroke="#1b8fd6" stroke-width="1.4"/></svg>Argan oil</li>
      <li><svg width="11" height="11" viewBox="0 0 11 11"><rect x=".5" y="1.5" width="9" height="9" fill="none" stroke="#1b8fd6"/><path d="M2.5 6l2 2 5-7" fill="none" stroke="#1b8fd6" stroke-width="1.4"/></svg>Prickly Pear seed oil</li>
      <li><svg width="11" height="11" viewBox="0 0 11 11"><rect x=".5" y="1.5" width="9" height="9" fill="none" stroke="#1b8fd6"/><path d="M2.5 6l2 2 5-7" fill="none" stroke="#1b8fd6" stroke-width="1.4"/></svg>Carrot oil</li>
      <li><svg width="11" height="11" viewBox="0 0 11 11"><rect x=".5" y="1.5" width="9" height="9" fill="none" stroke="#1b8fd6"/><path d="M2.5 6l2 2 5-7" fill="none" stroke="#1b8fd6" stroke-width="1.4"/></svg>Moroccan Beldi Soap</li>
      <li><svg width="11" height="11" viewBox="0 0 11 11"><rect x=".5" y="1.5" width="9" height="9" fill="none" stroke="#1b8fd6"/><path d="M2.5 6l2 2 5-7" fill="none" stroke="#1b8fd6" stroke-width="1.4"/></svg>Green Clay Mask</li>
      <li><svg width="11" height="11" viewBox="0 0 11 11"><rect x=".5" y="1.5" width="9" height="9" fill="none" stroke="#1b8fd6"/><path d="M2.5 6l2 2 5-7" fill="none" stroke="#1b8fd6" stroke-width="1.4"/></svg>Butter</li>
      <li class="tall"><svg width="11" height="11" viewBox="0 0 11 11"><rect x=".5" y="1.5" width="9" height="9" fill="none" stroke="#1b8fd6"/><path d="M2.5 6l2 2 5-7" fill="none" stroke="#1b8fd6" stroke-width="1.4"/></svg>Mineral and vegetable based<br>bar soaps</li>
      <li><svg width="11" height="11" viewBox="0 0 11 11"><rect x=".5" y="1.5" width="9" height="9" fill="none" stroke="#1b8fd6"/><path d="M2.5 6l2 2 5-7" fill="none" stroke="#1b8fd6" stroke-width="1.4"/></svg>Shea Butter</li>
      <li><svg width="11" height="11" viewBox="0 0 11 11"><rect x=".5" y="1.5" width="9" height="9" fill="none" stroke="#1b8fd6"/><path d="M2.5 6l2 2 5-7" fill="none" stroke="#1b8fd6" stroke-width="1.4"/></svg>Stretch marks/vergeture oil</li>
      <li><svg width="11" height="11" viewBox="0 0 11 11"><rect x=".5" y="1.5" width="9" height="9" fill="none" stroke="#1b8fd6"/><path d="M2.5 6l2 2 5-7" fill="none" stroke="#1b8fd6" stroke-width="1.4"/></svg>Massage oil</li>
    </ul>

    <div class="abs rule"></div>
    <div class="abs order">
      <svg width="36" height="31" viewBox="0 0 36 31" aria-hidden="true">
        <rect x="3" y="1" width="30" height="21" rx="2" fill="#f06a13"/>
        <rect x="6" y="4" width="24" height="15" fill="#fff"/>
        <path d="M15 8l6 4-3 .5 2 3-1 .6-2-3-2 2z" fill="#f06a13"/>
        <path d="M0 24h36l-2 5H2z" fill="#f06a13"/>
      </svg>
      <p>Place your order at<br>lumeranaturals.com</p>
    </div>

    <div class="abs contact">
      <h2>Contact us</h2>
      <p>(800) 555-0172</p>
      <p>hello@lumeranaturals.com</p>
      <p>www.lumeranaturals.com</p>
    </div>

    <div class="abs brand"><i></i>Lumera Naturals</div>

    <p class="abs tagline">Natural Solutions<span>to Forever Beauty</span></p>
  </section>

  <section class="panel panel--inner">
    <svg class="abs band" width="654" height="506" viewBox="0 0 654 506" aria-hidden="true">
      <defs>
        <linearGradient id="leafGlow" x1="0" y1="0" x2="1" y2="0">
          <stop offset="0" stop-color="#e8e3d8"/>
          <stop offset=".45" stop-color="#eef6e2"/>
          <stop offset="1" stop-color="#9fd05a"/>
        </linearGradient>
      </defs>
      <polygon points="0,0 654,0 654,64 0,162" fill="url(#leafGlow)"/>
      <polygon points="0,162 654,64 654,70 0,170" fill="#f06a13"/>
    </svg>

    <div class="photo" style="left:0;top:0;width:150px;height:158px;background:linear-gradient(135deg,#3a2418,#8a5a3c 60%,#d8c8b4)" role="img" aria-label="Woman with voluminous curly hair"></div>
    <div class="photo" style="left:100px;top:132px;width:92px;height:148px;border-radius:8px;background:linear-gradient(180deg,#c77a2e,#8a3f14 70%,#e3a12a)" role="img" aria-label="Amber oil bottles with a golden oil capsule"></div>
    <div class="photo" style="left:500px;top:26px;width:146px;height:102px;border-radius:8px;background:linear-gradient(135deg,#8fc7a0,#2f6bb0 55%,#e0603a)" role="img" aria-label="Boxed soap bars with lemon and prickly pear fruit"></div>
    <div class="photo" style="left:336px;top:244px;width:80px;height:100px;border-radius:8px;background:linear-gradient(180deg,#f2f2ec,#b9d8b0)" role="img" aria-label="Jar of cream and green clay mask box"></div>
    <div class="photo" style="left:236px;top:352px;width:180px;height:154px;background:linear-gradient(180deg,#ffffff,#efe4da 60%,#f7f3ef)" role="img" aria-label="Woman in a white towel seated with knees drawn up"></div>
    <div class="photo" style="left:606px;top:340px;width:40px;height:106px;border-radius:6px;background:linear-gradient(180deg,#2a2a2a,#3a2a5a 55%,#c23a3a)" role="img" aria-label="Massage oil spray bottle"></div>
    <div class="photo" style="left:562px;top:452px;width:88px;height:48px;border-radius:24px;background:radial-gradient(circle at 50% 50%,#c23a3a,#e8c9c0 70%,rgba(255,255,255,0))" role="img" aria-label="Cluster of red berries"></div>

    <h2 class="cat cat--orange" style="left:18px;top:262px">Hair &amp;<br>Skincare</h2>
    <div class="line line--orange" style="left:0;top:322px;width:163px"></div>
    <ul class="benefits" style="left:20px;top:338px">
      <li><svg width="11" height="11" viewBox="0 0 11 11"><rect x=".5" y="1.5" width="9" height="9" fill="none" stroke="#f06a13"/><path d="M2.5 6l2 2 5-7" fill="none" stroke="#f06a13" stroke-width="1.4"/></svg>Natural moisturizer</li>
      <li><svg width="11" height="11" viewBox="0 0 11 11"><rect x=".5" y="1.5" width="9" height="9" fill="none" stroke="#f06a13"/><path d="M2.5 6l2 2 5-7" fill="none" stroke="#f06a13" stroke-width="1.4"/></svg>Heal damaged hair or sensitive scalp</li>
      <li><svg width="11" height="11" viewBox="0 0 11 11"><rect x=".5" y="1.5" width="9" height="9" fill="none" stroke="#f06a13"/><path d="M2.5 6l2 2 5-7" fill="none" stroke="#f06a13" stroke-width="1.4"/></svg>Soften curly and frizzy hair</li>
      <li><svg width="11" height="11" viewBox="0 0 11 11"><rect x=".5" y="1.5" width="9" height="9" fill="none" stroke="#f06a13"/><path d="M2.5 6l2 2 5-7" fill="none" stroke="#f06a13" stroke-width="1.4"/></svg>Antiaging, remove wrinkles</li>
      <li><svg width="11" height="11" viewBox="0 0 11 11"><rect x=".5" y="1.5" width="9" height="9" fill="none" stroke="#f06a13"/><path d="M2.5 6l2 2 5-7" fill="none" stroke="#f06a13" stroke-width="1.4"/></svg>Reduce sebum secretion</li>
      <li><svg width="11" height="11" viewBox="0 0 11 11"><rect x=".5" y="1.5" width="9" height="9" fill="none" stroke="#f06a13"/><path d="M2.5 6l2 2 5-7" fill="none" stroke="#f06a13" stroke-width="1.4"/></svg>Tone, sooth and restore luster</li>
      <li><svg width="11" height="11" viewBox="0 0 11 11"><rect x=".5" y="1.5" width="9" height="9" fill="none" stroke="#f06a13"/><path d="M2.5 6l2 2 5-7" fill="none" stroke="#f06a13" stroke-width="1.4"/></svg>Restore fair complexion</li>
    </ul>

    <h2 class="cat cat--blue" style="left:230px;top:146px">Facial Care</h2>
    <div class="line line--blue" style="left:216px;top:182px;width:163px"></div>
    <ul class="benefits" style="left:232px;top:200px">
      <li><svg width="11" height="11" viewBox="0 0 11 11"><rect x=".5" y="1.5" width="9" height="9" fill="none" stroke="#1b8fd6"/><path d="M2.5 6l2 2 5-7" fill="none" stroke="#1b8fd6" stroke-width="1.4"/></svg>Reduce sebum secretion</li>
      <li><svg width="11" height="11" viewBox="0 0 11 11"><rect x=".5" y="1.5" width="9" height="9" fill="none" stroke="#1b8fd6"/><path d="M2.5 6l2 2 5-7" fill="none" stroke="#1b8fd6" stroke-width="1.4"/></svg>Eliminate toxins &amp; blemishes</li>
      <li><svg width="11" height="11" viewBox="0 0 11 11"><rect x=".5" y="1.5" width="9" height="9" fill="none" stroke="#1b8fd6"/><path d="M2.5 6l2 2 5-7" fill="none" stroke="#1b8fd6" stroke-width="1.4"/></svg>Tighten pores</li>
      <li><svg width="11" height="11" viewBox="0 0 11 11"><rect x=".5" y="1.5" width="9" height="9" fill="none" stroke="#1b8fd6"/><path d="M2.5 6l2 2 5-7" fill="none" stroke="#1b8fd6" stroke-width="1.4"/></svg>Dries pimples</li>
      <li class="tall"><svg width="11" height="11" viewBox="0 0 11 11"><rect x=".5" y="1.5" width="9" height="9" fill="none" stroke="#1b8fd6"/><path d="M2.5 6l2 2 5-7" fill="none" stroke="#1b8fd6" stroke-width="1.4"/></svg>Remove<br>blackheads</li>
    </ul>

    <h2 class="cat cat--orange" style="left:448px;top:134px">Body &amp;<br>Bath Care</h2>
    <div class="line line--orange" style="left:436px;top:199px;width:164px"></div>
    <ul class="benefits" style="left:449px;top:218px">
      <li><svg width="11" height="11" viewBox="0 0 11 11"><rect x=".5" y="1.5" width="9" height="9" fill="none" stroke="#f06a13"/><path d="M2.5 6l2 2 5-7" fill="none" stroke="#f06a13" stroke-width="1.4"/></svg>Purify and disinfect</li>
      <li><svg width="11" height="11" viewBox="0 0 11 11"><rect x=".5" y="1.5" width="9" height="9" fill="none" stroke="#f06a13"/><path d="M2.5 6l2 2 5-7" fill="none" stroke="#f06a13" stroke-width="1.4"/></svg>Fight acne</li>
      <li><svg width="11" height="11" viewBox="0 0 11 11"><rect x=".5" y="1.5" width="9" height="9" fill="none" stroke="#f06a13"/><path d="M2.5 6l2 2 5-7" fill="none" stroke="#f06a13" stroke-width="1.4"/></svg>Rejuvenate &amp; hydrate</li>
      <li><svg width="11" height="11" viewBox="0 0 11 11"><rect x=".5" y="1.5" width="9" height="9" fill="none" stroke="#f06a13"/><path d="M2.5 6l2 2 5-7" fill="none" stroke="#f06a13" stroke-width="1.4"/></svg>Promote healthy looking skin</li>
      <li><svg width="11" height="11" viewBox="0 0 11 11"><rect x=".5" y="1.5" width="9" height="9" fill="none" stroke="#f06a13"/><path d="M2.5 6l2 2 5-7" fill="none" stroke="#f06a13" stroke-width="1.4"/></svg>Remove dead cells</li>
    </ul>

    <h2 class="cat cat--blue" style="left:448px;top:330px">Massage Care</h2>
    <div class="line line--blue" style="left:436px;top:366px;width:164px"></div>
    <ul class="benefits" style="left:449px;top:384px">
      <li><svg width="11" height="11" viewBox="0 0 11 11"><rect x=".5" y="1.5" width="9" height="9" fill="none" stroke="#1b8fd6"/><path d="M2.5 6l2 2 5-7" fill="none" stroke="#1b8fd6" stroke-width="1.4"/></svg>Relief stress and pain</li>
      <li class="tall"><svg width="11" height="11" viewBox="0 0 11 11"><rect x=".5" y="1.5" width="9" height="9" fill="none" stroke="#1b8fd6"/><path d="M2.5 6l2 2 5-7" fill="none" stroke="#1b8fd6" stroke-width="1.4"/></svg>Fight muscle<br>contraction/tenderness</li>
      <li><svg width="11" height="11" viewBox="0 0 11 11"><rect x=".5" y="1.5" width="9" height="9" fill="none" stroke="#1b8fd6"/><path d="M2.5 6l2 2 5-7" fill="none" stroke="#1b8fd6" stroke-width="1.4"/></svg>Eliminate stretch marks</li>
      <li><svg width="11" height="11" viewBox="0 0 11 11"><rect x=".5" y="1.5" width="9" height="9" fill="none" stroke="#1b8fd6"/><path d="M2.5 6l2 2 5-7" fill="none" stroke="#1b8fd6" stroke-width="1.4"/></svg>Pure, undiluted</li>
    </ul>
  </section>

</div>
</body>
</html>
```